New Business Card Design Project

Use the flyer uploaded and website www.brightoakbuilders.com for inspiration.
List Our Services on Backside of business cards
Marcus Delling
Harborline Builders Inc.
Licensed General Contractors
858-471-6093

Contact Information for Business Card

Use the flyer uploaded and website www.brightoakbuilders.com for inspiration. List Our Services on Backside of business cards Marcus Delling Harborline Builders Inc. Licensed General Contractors 858-471-6093

```html
<!DOCTYPE html>
<html lang="en">
<head>
<meta charset="utf-8">
<title>Harborline Builders – Business Card</title>
<link href="https://fonts.googleapis.com/css2?family=Open+Sans:ital,wght@0,400;0,600;0,700;0,800;1,800&display=swap" rel="stylesheet">
<style>
  :root {
    --stage: #1b1b1d;
    --card: #222226;
    --ink: #f2f2f2;
    --muted: #d8d8d8;
    --red: #e31b23;
    --blue: #4a7fd6;
    --white-band: #e6e6e6;
    --rule: #cfcfcf;
  }
  * { margin: 0; padding: 0; box-sizing: border-box; }
  html, body { width: 1200px; height: 780px; overflow: hidden; background: var(--stage); }
  body { position: relative; font-family: "Open Sans", Arial, sans-serif; color: var(--ink); }

  .card {
    position: absolute; top: 230px; width: 560px; height: 320px;
    background: var(--card); border-radius: 22px; overflow: hidden;
    box-shadow: 0 12px 30px rgba(0,0,0,.45);
  }
  .card--front { left: 27px; }
  .card--back { left: 613px; }

  .brand { position: absolute; display: flex; align-items: center; gap: 12px; }
  .brand__mark { width: 16px; height: 16px; border: 1.5px solid var(--ink); flex: none; }
  .brand__name { font-weight: 400; letter-spacing: 2px; text-transform: uppercase; color: var(--ink); line-height: 1.15; }
  .brand__name span { display: block; }
  .card--front .brand { left: 40px; top: 96px; }
  .card--front .brand__name { font-size: 22px; }
  .card--back .brand { left: 44px; top: 118px; }
  .card--back .brand__name { font-size: 25px; }

  .edge-band { position: absolute; left: 0; bottom: 0; width: 560px; height: 40px; }

  .divider { position: absolute; left: 252px; top: 58px; width: 1px; height: 190px; background: var(--rule); }

  .contact-block { position: absolute; left: 272px; top: 66px; }
  .person__name { font-size: 25px; font-weight: 800; color: var(--red); text-transform: uppercase; line-height: 1.15; white-space: nowrap; margin-bottom: 4px; }
  .person__role, .person__company { font-size: 14px; color: var(--ink); line-height: 1.55; white-space: nowrap; }
  .person__company { margin-bottom: 14px; }
  .contact-list { list-style: none; }
  .contact-list li { display: flex; align-items: center; gap: 9px; font-size: 14px; line-height: 1.75; white-space: nowrap; }
  .contact-list svg { width: 13px; height: 13px; flex: none; }

  .services { position: absolute; left: 316px; top: 44px; width: 226px; }
  .services__claim { font-size: 14px; font-weight: 800; font-style: italic; color: var(--red); text-transform: uppercase; line-height: 1.2; }
  .services__lead { font-size: 14px; font-weight: 800; font-style: italic; color: var(--blue); text-transform: uppercase; line-height: 1.4; margin-bottom: 4px; }
  .service-list { list-style: none; }
  .service-list li { display: flex; align-items: center; gap: 7px; font-size: 12px; font-weight: 600; line-height: 20px; white-space: nowrap; }
  .service-list svg { width: 12px; height: 12px; flex: none; }
</style>
</head>
<body>

<section class="card card--front" aria-label="Business card front">
  <div class="brand">
    <span class="brand__mark"></span>
    <span class="brand__name"><span>Harborline</span><span>Builders</span></span>
  </div>

  <div class="divider"></div>

  <div class="contact-block">
    <h1 class="person__name">Marcus Delling</h1>
    <p class="person__role">Licensed General Contractors</p>
    <p class="person__company">Harborline Builders Inc.</p>
    <ul class="contact-list">
      <li>
        <svg viewBox="0 0 16 16"><path fill="var(--red)" d="M3.6 1.2l2.3 2.6-1.3 1.9c.9 2 2.4 3.6 4.5 4.6l1.9-1.3 2.6 2.3-1.5 2.9C6.8 13.7 2.3 9.2 1 3z"/></svg>
        858-471-6093
      </li>
      <li>
        <svg viewBox="0 0 16 16"><rect x="1" y="3" width="14" height="10" rx="1.5" fill="var(--red)"/><path d="M1.5 4l6.5 5 6.5-5" fill="none" stroke="var(--card)" stroke-width="1.4"/></svg>
        info@brightoakbuilders.com
      </li>
      <li>
        <svg viewBox="0 0 16 16"><circle cx="8" cy="8" r="7" fill="var(--red)"/><path d="M1 8h14M8 1c-3 3.5-3 10.5 0 14M8 1c3 3.5 3 10.5 0 14" fill="none" stroke="var(--card)" stroke-width="1"/></svg>
        www.brightoakbuilders.com
      </li>
    </ul>
  </div>

  <svg class="edge-band" viewBox="0 0 560 40" preserveAspectRatio="none" aria-hidden="true">
    <polygon points="0,8 240,8 252,40 0,40" fill="var(--red)"/>
    <polygon points="258,22 560,22 560,40 266,40" fill="var(--white-band)"/>
  </svg>
</section>

<section class="card card--back" aria-label="Business card back">
  <div class="brand">
    <span class="brand__mark"></span>
    <span class="brand__name"><span>Harborline</span><span>Builders</span></span>
  </div>

  <div class="services">
    <p class="services__claim">Our services are<br>100% guaranteed</p>
    <p class="services__lead">Specializing in:</p>
    <ul class="service-list">
      <li><svg viewBox="0 0 12 12"><circle cx="6" cy="6" r="5" fill="none" stroke="var(--red)" stroke-width="1.3"/><path d="M3.5 6l1.8 1.8L8.6 4.3" fill="none" stroke="var(--red)" stroke-width="1.4"/></svg>Remodel: Kitchen &amp; Bath</li>
      <li><svg viewBox="0 0 12 12"><circle cx="6" cy="6" r="5" fill="none" stroke="var(--red)" stroke-width="1.3"/><path d="M3.5 6l1.8 1.8L8.6 4.3" fill="none" stroke="var(--red)" stroke-width="1.4"/></svg>Painting: Interior &amp; Exterior</li>
      <li><svg viewBox="0 0 12 12"><circle cx="6" cy="6" r="5" fill="none" stroke="var(--red)" stroke-width="1.3"/><path d="M3.5 6l1.8 1.8L8.6 4.3" fill="none" stroke="var(--red)" stroke-width="1.4"/></svg>Flooring: Carpet, Vinyl, Wood</li>
      <li><svg viewBox="0 0 12 12"><circle cx="6" cy="6" r="5" fill="none" stroke="var(--red)" stroke-width="1.3"/><path d="M3.5 6l1.8 1.8L8.6 4.3" fill="none" stroke="var(--red)" stroke-width="1.4"/></svg>Window &amp; Door Replacement</li>
      <li><svg viewBox="0 0 12 12"><circle cx="6" cy="6" r="5" fill="none" stroke="var(--red)" stroke-width="1.3"/><path d="M3.5 6l1.8 1.8L8.6 4.3" fill="none" stroke="var(--red)" stroke-width="1.4"/></svg>Plumbing: Repairs &amp; Upgrades</li>
      <li><svg viewBox="0 0 12 12"><circle cx="6" cy="6" r="5" fill="none" stroke="var(--red)" stroke-width="1.3"/><path d="M3.5 6l1.8 1.8L8.6 4.3" fill="none" stroke="var(--red)" stroke-width="1.4"/></svg>Energy-Efficient Upgrades</li>
      <li><svg viewBox="0 0 12 12"><circle cx="6" cy="6" r="5" fill="none" stroke="var(--red)" stroke-width="1.3"/><path d="M3.5 6l1.8 1.8L8.6 4.3" fill="none" stroke="var(--red)" stroke-width="1.4"/></svg>Deck &amp; Patio Construction</li>
      <li><svg viewBox="0 0 12 12"><circle cx="6" cy="6" r="5" fill="none" stroke="var(--red)" stroke-width="1.3"/><path d="M3.5 6l1.8 1.8L8.6 4.3" fill="none" stroke="var(--red)" stroke-width="1.4"/></svg>Water &amp; Mold Damage</li>
      <li><svg viewBox="0 0 12 12"><circle cx="6" cy="6" r="5" fill="none" stroke="var(--red)" stroke-width="1.3"/><path d="M3.5 6l1.8 1.8L8.6 4.3" fill="none" stroke="var(--red)" stroke-width="1.4"/></svg>Garage Renovation</li>
    </ul>
  </div>
</section>

</body>
</html>
```